Dorven GYM

customer is looking for a quiet, but present design on his silver-colored KX transporter. https://dorvengym.example/

the design can be like half if a wrap, with a nice picture in the background and his logo on top of it

I will attach some files

```html
<!DOCTYPE html>
<html lang="nl">
<head>
<meta charset="utf-8">
<title>Dorven GYM – van wrap</title>
<link rel="stylesheet" href="https://fonts.googleapis.com/css2?family=Anton&family=Bebas+Neue&family=Oswald:wght@400;500&family=Roboto+Slab:wght@800&display=swap">
<style>
  :root {
    --backdrop: #eceded;
    --body-silver: #7e7f81;
    --body-shade: #5f6062;
    --glass: #3a4148;
    --ink: #1c1c1e;
    --brand-blue: #1ba0dc;
    --brand-blue-dark: #11709c;
    --white: #ffffff;
    --tyre: #1f1f20;
    --rim: #b9bcbf;
  }
  html, body {
    margin: 0;
    padding: 0;
    overflow: hidden;
    background: var(--backdrop);
  }
  .canvas {
    width: 1200px;
    height: 708px;
    display: block;
    background: var(--backdrop);
  }
  .van-body { fill: var(--body-silver); }
  .panel-line { fill: none; stroke: var(--body-shade); stroke-width: 2; }
  .glass { fill: var(--glass); }
  .tyre { fill: var(--tyre); }
  .rim { fill: var(--rim); }
  .hub { fill: #8d9093; }
  .quote { font-family: "Bebas Neue", sans-serif; font-size: 32px; fill: var(--white); }
  .quote-credit { font-family: "Bebas Neue", sans-serif; font-size: 17px; fill: var(--white); }
  .phone { font-family: "Bebas Neue", sans-serif; font-size: 56px; fill: var(--ink); }
  .web { font-family: "Bebas Neue", sans-serif; font-size: 31px; fill: var(--ink); }
  .logo-plate { fill: var(--ink); stroke: var(--white); stroke-width: 3; }
  .logo-name { font-family: "Anton", sans-serif; font-size: 96px; fill: var(--white); letter-spacing: 2px; }
  .logo-sub { font-family: "Oswald", sans-serif; font-weight: 400; font-size: 40px; fill: var(--brand-blue); }
  .service { font-family: "Roboto Slab", serif; font-weight: 800; font-size: 22px; fill: var(--ink); }
  .service-dot { fill: var(--white); }
  .offer-band { fill: var(--brand-blue); }
  .offer-band-edge { fill: var(--brand-blue-dark); }
  .offer { font-family: "Bebas Neue", sans-serif; font-size: 38px; fill: var(--ink); }
  .offer-hi { fill: var(--white); }
  .social-dot { fill: var(--brand-blue); }
  .social-handle { font-family: "Bebas Neue", sans-serif; font-size: 24px; fill: var(--white); }
  .lamp { fill: #2a2c2e; }
  .tail-lamp { fill: #b3262b; }
</style>
</head>
<body>
<svg class="canvas" viewBox="0 0 1494 882" width="1200" height="708" xmlns="http://www.w3.org/2000/svg">
  <defs>
    <clipPath id="body-clip">
      <path d="M40,645 L30,545 Q34,455 92,425 L262,362 Q380,232 472,206 L1372,190 Q1418,198 1440,330 L1466,600 L1460,645 Z"/>
    </clipPath>
    <linearGradient id="athlete-tones" x1="0" y1="0" x2="1" y2="1">
      <stop offset="0" stop-color="#2a2422"/>
      <stop offset="0.35" stop-color="#6e4a38"/>
      <stop offset="0.6" stop-color="#8a5e48"/>
      <stop offset="1" stop-color="#1a1818"/>
    </linearGradient>
  </defs>

  <!-- van body -->
  <path class="van-body" d="M40,645 L30,545 Q34,455 92,425 L262,362 Q380,232 472,206 L1372,190 Q1418,198 1440,330 L1466,600 L1460,645 Z"/>

  <!-- photo side of the wrap -->
  <g clip-path="url(#body-clip)">
    <polygon role="img" aria-label="Photo of a muscular athlete lifting a weight plate, dark gym background"
      fill="url(#athlete-tones)"
      points="1118,180 1098,232 1090,292 1066,352 1050,420 1034,470 994,520 964,560 948,650 1480,650 1480,180"/>
  </g>

  <!-- panel lines -->
  <line class="panel-line" x1="628" y1="208" x2="628" y2="590"/>
  <line class="panel-line" x1="295" y1="380" x2="298" y2="590"/>
  <line class="panel-line" x1="965" y1="212" x2="1100" y2="210"/>

  <!-- window -->
  <polygon class="glass" points="352,372 384,292 462,226 606,216 606,370"/>

  <!-- lights -->
  <path class="lamp" d="M48,470 L128,432 L118,462 L52,492 Z"/>
  <rect class="tail-lamp" x="1416" y="410" width="18" height="70" rx="4"/>

  <!-- wheels -->
  <circle class="tyre" cx="228" cy="632" r="104"/>
  <circle class="rim" cx="228" cy="632" r="70"/>
  <circle class="hub" cx="228" cy="632" r="18"/>
  <circle class="tyre" cx="1214" cy="642" r="104"/>
  <circle class="rim" cx="1214" cy="642" r="70"/>
  <circle class="hub" cx="1214" cy="642" r="18"/>

  <!-- quote -->
  <text class="quote" x="648" y="246">DO IT NOW DON’T WAIT</text>
  <text class="quote" x="648" y="276">FOR TOMMORROW</text>
  <text class="quote-credit" x="650" y="298">(MARTEN VOS)</text>

  <!-- contact -->
  <text class="phone" x="336" y="480">06-48193527</text>
  <text class="web" x="337" y="516">WWW.DORVENGYM.EXAMPLE</text>

  <!-- brand name -->
  <rect class="logo-plate" x="626" y="328" width="520" height="118"/>
  <text class="logo-name" x="886" y="428" text-anchor="middle">DORVEN GYM</text>
  <text class="logo-sub" x="1158" y="404">TRAINING</text>
  <text class="logo-sub" x="1158" y="448">CENTRE</text>

  <!-- services -->
  <g class="services">
    <text class="service" x="964" y="465" text-anchor="end">CARDIO</text>
    <text class="service" x="964" y="489" text-anchor="end">KRACTTRAINING</text>
    <text class="service" x="964" y="513" text-anchor="end">GROEPSLESSEN</text>
    <text class="service" x="964" y="537" text-anchor="end">KIDSLESSEN</text>
    <circle class="service-dot" cx="977" cy="458" r="5"/>
    <circle class="service-dot" cx="977" cy="482" r="5"/>
    <circle class="service-dot" cx="977" cy="506" r="5"/>
    <circle class="service-dot" cx="977" cy="530" r="5"/>
  </g>

  <!-- social -->
  <circle class="social-dot" cx="1024" cy="575" r="14"/>
  <text class="social-handle" x="1046" y="584">@DORVENGYM</text>

  <!-- offer band -->
  <polygon class="offer-band" points="340,590 946,590 942,642 344,642"/>
  <polygon class="offer-band-edge" points="344,636 942,636 942,642 344,642"/>
  <text class="offer" x="360" y="630">WIJ NODIGEN JE UIT VOOR EEN <tspan class="offer-hi">GRATIS</tspan> PROEFLES!</text>
</svg>
</body>
</html>
```